Brookvale Estates LLC stationary for a real estate property management company.

Create stationary (letterhead, envelopes, business cards) using Brookvale Estates LLC logo as primary creative element. Stationary design needs to be horizontal, leaving as much space as possible for correspondence copy. See attached Creative Brief and past stationary files for details.

Target Market(s)

Prospective apartment residents and current residents, vendors, and government agencies.

Industry/Entity Type

Property Management

Contact Information for Business Card

Business card employee title: Property Manager. Should include address, phone, fax, email, website, slogan, and Brookvale Estates logo.

Font styles to use
Sans Serif

Colors
0592cd
000000

Requirements
Must have
• Tone should be conservative, institutional, business (i.e. banking, finance, real estate). Must include: address, phone, fax, website, and slogan (see attached Creative Brief). Should be a horizontal design, leaving as much room as possible for letter correspondence copy.
Nice to have
• Please use an Arial or Helvetica style font.
Should not have
• Letterhead layout should leave as much room as possible for copy.

```html
<!DOCTYPE html>
<html lang="en">
<head>
<meta charset="utf-8">
<title>Brookvale Estates LLC – Stationery</title>
<link href="https://fonts.googleapis.com/css2?family=Arimo:wght@400;700&display=swap" rel="stylesheet">
<style>
  :root {
    --brand-blue: #1b75b0;
    --ink: #2a2a2a;
    --paper: #ffffff;
    --backdrop: #ececec;
    --muted: #555555;
  }
  * { margin: 0; padding: 0; box-sizing: border-box; }
  html, body { width: 1200px; height: 938px; overflow: hidden; background: var(--backdrop); }
  body { font-family: "Arimo", Arial, sans-serif; color: var(--ink); }
  .stage { position: relative; width: 1200px; height: 938px; overflow: hidden; }
  .sheet { position: absolute; background: var(--paper); overflow: hidden; box-shadow: 0 1px 3px rgba(0,0,0,.12); }
  .abs { position: absolute; }

  /* wordmark */
  .wordmark { position: absolute; display: flex; align-items: center; gap: 6px; }
  .wordmark .mark { background: var(--ink); flex: none; }
  .wordmark .name { color: var(--brand-blue); font-weight: 700; line-height: 1; letter-spacing: .02em; text-transform: uppercase; }
  .slogan { position: absolute; color: var(--muted); font-style: normal; letter-spacing: .04em; white-space: nowrap; }

  /* letterhead */
  .letterhead { left: 184px; top: 67px; width: 388px; height: 546px; }
  .letter { position: absolute; left: 38px; top: 142px; width: 294px; font-size: 5.6px; line-height: 8.4px; color: #333; }
  .letter p { margin-bottom: 8px; }
  .letter .strong { font-weight: 700; }
  .signature { width: 40px; height: 22px; background: #e6e6e6; margin: 6px 0 8px; }
  .contact { position: absolute; left: 47px; font-size: 5px; line-height: 6.6px; color: #333; white-space: nowrap; }
  .contact.center { text-align: center; }

  /* folder */
  .folder { left: 636px; top: 42px; width: 460px; height: 574px; }
  .folder-url { position: absolute; left: 62px; top: 533px; font-size: 10px; letter-spacing: .25em; color: #e4e4e4; }

  /* cards */
  .card-front { left: 46px; top: 660px; width: 176px; height: 98px; }
  .card-back { left: 46px; top: 786px; width: 176px; height: 99px; }
  .card-contact { position: absolute; right: 100px; font-size: 4.4px; line-height: 5.8px; color: #fff; text-align: right; white-space: nowrap; }
  .card-person { position: absolute; right: 10px; top: 76px; text-align: right; font-size: 6px; line-height: 7.2px; color: #222; }

  /* envelopes */
  .envelope-dl { left: 266px; top: 674px; width: 430px; height: 208px; }
  .envelope-back { left: 736px; top: 672px; width: 434px; height: 208px; }
  .env-url { position: absolute; font-size: 9.5px; letter-spacing: .2em; color: #333; }
  .flap { position: absolute; left: 0; top: 0; width: 434px; height: 72px; background: var(--brand-blue); border-radius: 0 0 38px 38px; }
  .flap-url { position: absolute; left: 0; right: 0; top: 30px; text-align: center; color: #fff; font-size: 12px; letter-spacing: .28em; }
</style>
</head>
<body>
<main class="stage">

  <!-- Letterhead -->
  <section class="sheet letterhead" aria-label="Letterhead">
    <svg class="abs" style="left:0;top:0" width="60" height="546" viewBox="0 0 60 546" aria-hidden="true">
      <path d="M0 0 H28 V452 Q28 460 38 466 V522 Q28 528 28 536 V546 H0 Z" fill="var(--brand-blue)"/>
      <g fill="var(--brand-blue)" stroke="#fff" stroke-width="1">
        <circle cx="30" cy="470" r="7"/>
        <circle cx="30" cy="494" r="7"/>
        <circle cx="30" cy="518" r="7"/>
      </g>
      <g fill="none" stroke="#fff" stroke-width="0.9" stroke-linecap="round">
        <path d="M27.5 467 q-1 3 2 6 q1 1 3 0"/>
        <path d="M30 498 c-3 -3 -3 -5 -3 -6 a3 3 0 0 1 6 0 c0 1 0 3 -3 6z"/>
        <circle cx="30" cy="518" r="3.5"/><path d="M26.5 518 h7 M30 514.5 v7"/>
      </g>
    </svg>

    <div class="wordmark" style="left:40px;top:44px">
      <span class="mark" style="width:20px;height:20px"></span>
      <span class="name" style="font-size:13px">Brookvale<br>Estates LLC</span>
    </div>
    <p class="slogan" style="left:40px;top:74px;font-size:6px">Homes Managed With Care</p>

    <div class="letter">
      <p>July 2, 2012</p>
      <p><span class="strong">Dear Ms. Lane,</span><br>Elm Court, 22 Garden St., Northfield</p>
      <p style="margin-top:14px">Thank you for your interest in our residential communities. Our team manages apartment homes across the region and takes pride in keeping every property safe, clean and well maintained. We respond to service requests promptly and keep residents informed about building updates, inspections and community events. This letter confirms the details of your upcoming lease review and the documents needed for renewal.</p>
      <p style="margin-top:16px">Please bring a valid photo ID and proof of income to our leasing office. Appointments can be scheduled by phone or email during regular business hours.</p>
      <p style="margin-top:24px">We value our partnership with residents, vendors and local agencies alike. Should you have any questions about maintenance schedules, parking arrangements or rent payment options, our staff will be glad to assist you. We look forward to welcoming you for another year and to continuing to provide a comfortable, well managed home for you and your family.</p>
      <p>Best Regards,</p>
      <div class="signature" role="img" aria-label="Handwritten signature"></div>
      <p style="margin-bottom:0"><span class="strong">Daniel Reyes</span><br>Director</p>
      <p style="margin-top:3px">Elm Court, 22 Garden St., Northfield</p>
    </div>

    <div class="contact" style="top:464px">Tel 012 555 0147<br>Fax 012 555 0148</div>
    <div class="contact center" style="top:488px;left:40px;width:64px">Suite 410, Harbor Lane,<br>Northfield</div>
    <div class="contact" style="top:512px">office@brookvaleestates.com<br>www.brookvaleestates.com</div>
  </section>

  <!-- Presentation folder -->
  <section class="sheet folder" aria-label="Presentation folder">
    <svg class="abs" style="left:0;top:0" width="60" height="574" viewBox="0 0 60 574" aria-hidden="true">
      <defs>
        <linearGradient id="spineShade" x1="0" x2="1">
          <stop offset="0" stop-color="#e6e6e6"/><stop offset="1" stop-color="#cfcfcf"/>
        </linearGradient>
      </defs>
      <path d="M0 0 H41 V515 Q41 522 50 528 V552 Q41 558 41 566 V574 H0 Z" fill="url(#spineShade)"/>
      <circle cx="41" cy="538" r="8" fill="#f2f2f2" stroke="#444" stroke-width="1"/>
      <g fill="none" stroke="#444" stroke-width="0.8">
        <circle cx="41" cy="538" r="4.5"/><path d="M36.5 538 h9 M41 533.5 v9"/>
      </g>
    </svg>
    <div class="wordmark" style="left:110px;top:256px">
      <span class="mark" style="width:56px;height:56px"></span>
      <span class="name" style="font-size:31px">Brookvale<br>Estates LLC</span>
    </div>
    <div class="folder-url">www.brookvaleestates.com</div>
  </section>

  <!-- Business card front -->
  <section class="sheet card-front" aria-label="Business card front">
    <svg class="abs" style="left:0;top:0" width="100" height="98" viewBox="0 0 100 98" aria-hidden="true">
      <path d="M0 0 H80 V14 Q80 20 88 24 V80 Q80 84 80 90 V98 H0 Z" fill="var(--brand-blue)"/>
      <g fill="var(--brand-blue)" stroke="#fff" stroke-width="0.9">
        <circle cx="82" cy="23" r="6"/><circle cx="82" cy="47" r="6"/><circle cx="82" cy="71" r="6"/>
      </g>
      <g fill="none" stroke="#fff" stroke-width="0.8" stroke-linecap="round">
        <path d="M80 20.5 q-1 3 2 5 q1 1 2.5 0"/>
        <path d="M82 50 c-2.5 -2.5 -2.5 -4 -2.5 -5 a2.5 2.5 0 0 1 5 0 c0 1 0 2.5 -2.5 5z"/>
        <circle cx="82" cy="71" r="3"/><path d="M79 71 h6 M82 68 v6"/>
      </g>
    </svg>
    <div class="card-contact" style="top:18px">Tel 012 555 0147<br>Fax 012 555 0148</div>
    <div class="card-contact" style="top:42px">Suite 410, Harbor Lane,<br>Northfield</div>
    <div class="card-contact" style="top:66px">office@brookvaleestates.com<br>brookvaleestates.com</div>
    <div class="wordmark" style="left:100px;top:20px">
      <span class="mark" style="width:11px;height:11px"></span>
      <span class="name" style="font-size:7.5px">Brookvale<br>Estates LLC</span>
    </div>
    <p class="slogan" style="left:100px;top:40px;font-size:4.6px">Homes Managed With Care</p>
    <div class="card-person">MARCUS HALE<br>Property Manager</div>
  </section>

  <!-- Business card back -->
  <section class="sheet card-back" aria-label="Business card back">
    <div class="wordmark" style="left:50px;top:36px">
      <span class="mark" style="width:18px;height:18px"></span>
      <span class="name" style="font-size:10.5px">Brookvale<br>Estates LLC</span>
    </div>
    <p class="slogan" style="left:50px;top:62px;font-size:5.6px">Homes Managed With Care</p>
  </section>

  <!-- DL envelope front -->
  <section class="sheet envelope-dl" aria-label="Envelope front">
    <svg class="abs" style="left:0;top:0" width="40" height="208" viewBox="0 0 40 208" aria-hidden="true">
      <path d="M0 0 H22 V172 Q22 178 30 182 V196 Q22 200 22 204 V208 H0 Z" fill="var(--brand-blue)"/>
      <circle cx="20" cy="189" r="7" fill="var(--brand-blue)" stroke="#fff" stroke-width="1"/>
      <g fill="none" stroke="#fff" stroke-width="0.8">
        <circle cx="20" cy="189" r="3.6"/><path d="M16.4 189 h7.2 M20 185.4 v7.2"/>
      </g>
    </svg>
    <div class="wordmark" style="left:34px;top:32px">
      <span class="mark" style="width:20px;height:20px"></span>
      <span class="name" style="font-size:13px">Brookvale<br>Estates LLC</span>
    </div>
    <div class="env-url" style="left:37px;top:183px">www.brookvaleestates.com</div>
  </section>

  <!-- Envelope back -->
  <section class="sheet envelope-back" aria-label="Envelope back">
    <div class="flap"></div>
    <div class="flap-url">www.brookvaleestates.com</div>
  </section>

</main>
</body>
</html>
```